Veltrano.co - Polar Expeditions Specialists

We need a modern, visually striking business card for Veltrano.co, a company specialized in selling expedition cruises to the most remote regions on Earth, with a focus on the Arctic and Antarctica. The design should instantly communicate that the cardholder is an expert in polar travel. Use clean, premium aesthetics with cool tones like icy blue and white, possibly incorporating polar imagery (ice, glaciers, penguins, etc.)

Attached the logo

Contact Information for Business Card

Feels high-end and trustworthy.. Visually memorable — encourages people to keep it

Colors
0054AA
0677BA
7BADD7
CADEEF
E8F1F8

Requirements
Must have
• ice, glaciers, penguins, montains
Nice to have
• modern, transparente,

```html
<!DOCTYPE html>
<html lang="en">
<head>
<meta charset="utf-8">
<title>Veltrano.co Business Card</title>
<link href="https://fonts.googleapis.com/css2?family=Poppins:wght@400;500;700;800&display=swap" rel="stylesheet">
<style>
  :root {
    --brand-blue: #2f78be;
    --deep-blue: #0054aa;
    --ice-blue: #7badd7;
    --frost: #cadeef;
    --snow: #ffffff;
    --paper: #f7f8f9;
    --ink: #333a40;
    --stage: #d9dcdf;
  }
  html, body {
    margin: 0;
    padding: 0;
    width: 1200px;
    height: 788px;
    overflow: hidden;
    background: var(--stage);
    font-family: "Poppins", sans-serif;
  }
  .canvas {
    width: 1200px;
    height: 788px;
    display: flex;
    align-items: center;
    justify-content: center;
    gap: 40px;
  }
  .card {
    position: relative;
    width: 540px;
    height: 310px;
    border-radius: 22px;
    overflow: hidden;
    box-shadow: 0 10px 30px rgba(0,0,0,0.15);
  }

  /* Contact side */
  .card--contact { background: var(--paper); }
  .card__wave {
    position: absolute;
    inset: 0;
    width: 100%;
    height: 100%;
  }
  .brand {
    position: absolute;
    left: 34px;
    top: 150px;
    color: var(--brand-blue);
  }
  .brand__row { display: flex; align-items: center; gap: 7px; }
  .brand__dot {
    width: 12px; height: 12px;
    border-radius: 50%;
    background: var(--brand-blue);
  }
  .brand__name {
    font-weight: 800;
    font-size: 24px;
    line-height: 1;
  }
  .brand__tagline {
    margin: 4px 0 0 19px;
    font-weight: 700;
    font-size: 8px;
  }
  .divider {
    position: absolute;
    left: 248px;
    top: 36px;
    width: 1.5px;
    height: 150px;
    background: var(--brand-blue);
  }
  .contact {
    position: absolute;
    left: 268px;
    top: 26px;
    color: var(--ink);
    font-size: 11.5px;
    line-height: 1.45;
  }
  .contact__name {
    margin: 0;
    font-weight: 800;
    font-size: 21px;
    color: var(--brand-blue);
    letter-spacing: 0.5px;
    line-height: 1.1;
  }
  .contact__role { margin: 0 0 8px; font-size: 12.5px; }
  .contact__address { margin: 0 0 8px; }
  .contact__line { display: flex; align-items: center; gap: 6px; margin: 0; }
  .contact__icon { width: 11px; height: 11px; fill: var(--brand-blue); }
  .website {
    position: absolute;
    right: 30px;
    bottom: 22px;
    color: var(--snow);
    font-size: 13px;
    letter-spacing: 0.5px;
  }

  /* Brand side */
  .card--brand { background: var(--brand-blue); }
  .card__scenery {
    position: absolute;
    right: 30px;
    top: 0;
    width: 300px;
    height: 310px;
    background: radial-gradient(ellipse at 50% 60%, rgba(202,222,239,0.25), rgba(202,222,239,0) 70%);
  }
  .hero {
    position: absolute;
    left: 70px;
    top: 108px;
    color: var(--snow);
  }
  .hero__row { display: flex; align-items: center; gap: 12px; }
  .hero__dot {
    width: 22px; height: 22px;
    border-radius: 50%;
    background: var(--snow);
  }
  .hero__name {
    font-weight: 800;
    font-size: 58px;
    line-height: 1;
  }
  .hero__tagline {
    margin: 8px 0 0 36px;
    font-weight: 700;
    font-size: 17px;
  }
</style>
</head>
<body>
<main class="canvas">

  <section class="card card--contact" aria-label="Contact side">
    <svg class="card__wave" viewBox="0 0 540 310" preserveAspectRatio="none" aria-hidden="true">
      <path d="M0,296 C170,302 290,262 380,218 C450,186 495,180 540,178 L540,310 L0,310 Z" fill="var(--brand-blue)"/>
      <path d="M0,286 C170,294 290,250 380,206 C450,174 495,168 540,166" fill="none" stroke="var(--brand-blue)" stroke-width="2"/>
    </svg>

    <div class="brand">
      <div class="brand__row">
        <span class="brand__dot"></span>
        <span class="brand__name">Veltrano.co</span>
      </div>
      <p class="brand__tagline">Polar Expeditions Specialists</p>
    </div>

    <div class="divider"></div>

    <div class="contact">
      <h1 class="contact__name">MARCUS HALE</h1>
      <p class="contact__role">CEO / Founder</p>
      <p class="contact__address">P.O. Box 4127 Harbor Road<br>Northland NV 6120</p>
      <p class="contact__line">
        <svg class="contact__icon" viewBox="0 0 24 24"><path d="M6.6 10.8a15 15 0 0 0 6.6 6.6l2.2-2.2c.3-.3.7-.4 1-.2 1.1.4 2.3.6 3.6.6.6 0 1 .4 1 1V20c0 .6-.4 1-1 1A17 17 0 0 1 3 4c0-.6.4-1 1-1h3.5c.6 0 1 .4 1 1 0 1.3.2 2.5.6 3.6.1.3 0 .7-.2 1z"/></svg>
        +41 555 20 83 917
      </p>
      <p class="contact__line">
        <svg class="contact__icon" viewBox="0 0 24 24"><path d="M2 5h20v14H2z M2 5l10 8 10-8" stroke="var(--snow)" stroke-width="1.5"/></svg>
        marcus.hale@veltrano.co
      </p>
    </div>

    <span class="website">www.veltrano.co</span>
  </section>

  <section class="card card--brand" aria-label="Brand side">
    <div class="card__scenery" role="img" aria-label="Faint polar wildlife silhouettes with penguins"></div>
    <div class="hero">
      <div class="hero__row">
        <span class="hero__dot"></span>
        <span class="hero__name">Veltrano.co</span>
      </div>
      <p class="hero__tagline">Polar Expeditions Specialists</p>
    </div>
  </section>

</main>
</body>
</html>
```